Oliver + Rory's 30th Birthday FB event cover photo

We're after a Facebook even cover photo for our 30th B'day. We live in Sydney
Oliver + Rory's 30th Birthday

Venue (these details can be used in the graphic):
Quiet Heron
the basement of
The Walrus Hotel
214 Corran St Halvey
2 August 8pm-3am

The Walrus logo: http://www.thewalrushotel.example
Quiet Heron logo: http://quietheronpurr.example.au
The horizontal FaceBook cover photo for events has specific dimensions
As ideas I kind of like the styling of the dj poster (file attached) as a rough guide but not essential (i.e. no need to stick to that format/colours/dark shades) and Also the poster Pixel Bazaar's Morven did for Velvet Drift
Thanks!

```html
<!DOCTYPE html>
<html lang="en">
<head>
<meta charset="utf-8">
<title>Oliver + Rory's 30th Birthday – Event Cover</title>
<link rel="stylesheet" href="https://fonts.googleapis.com/css2?family=Bebas+Neue&display=swap">
<style>
  :root {
    --ink: #2b1f24;
    --white: #ffffff;
    --disc: #ffffff;
    --venue-mark: #4a2a78;
    --host-mark: #6b4a8f;
    --bokeh-deep: #1e1020;
    --bokeh-mid: #5a2a4e;
    --bokeh-warm: #c9708a;
    --bokeh-teal: #2f6f7a;
  }
  * { box-sizing: border-box; margin: 0; padding: 0; }
  html, body { width: 1200px; height: 452px; overflow: hidden; background: var(--bokeh-deep); }
  body { font-family: "Bebas Neue", "Oswald", sans-serif; }

  .cover {
    position: relative;
    width: 1200px;
    height: 452px;
    overflow: hidden;
    color: var(--white);
  }

  .cover__backdrop {
    position: absolute;
    inset: 0;
    background:
      radial-gradient(circle at 8% 30%, rgba(201,112,138,.55) 0, transparent 28%),
      radial-gradient(circle at 30% 75%, rgba(47,111,122,.55) 0, transparent 30%),
      radial-gradient(circle at 78% 40%, rgba(230,150,160,.45) 0, transparent 30%),
      radial-gradient(circle at 92% 80%, rgba(120,60,140,.5) 0, transparent 30%),
      linear-gradient(180deg, var(--bokeh-deep) 0%, var(--bokeh-mid) 55%, #3a1a34 100%);
  }

  .venue {
    position: absolute;
    left: 23px;
    top: 104px;
    line-height: 1;
    letter-spacing: 0.5px;
  }
  .venue__line { font-size: 46px; line-height: 42px; }
  .venue__address { font-size: 30px; line-height: 30px; margin-top: 2px; }

  .when {
    position: absolute;
    left: 940px;
    top: 154px;
    line-height: 1;
  }
  .when__date { font-size: 54px; line-height: 50px; }
  .when__time { font-size: 72px; line-height: 66px; }

  .badge {
    position: absolute;
    top: 330px;
    text-align: center;
    font-size: 54px;
    line-height: 44px;
    letter-spacing: 2px;
  }
  .badge--venue { left: 120px; color: var(--venue-mark); }
  .badge--host { left: 945px; color: var(--host-mark); letter-spacing: 6px; }

  .disc {
    position: absolute;
    left: 427px;
    top: 52px;
    width: 346px;
    height: 346px;
    border-radius: 50%;
    background: var(--disc);
    color: var(--ink);
    text-align: center;
    display: flex;
    flex-direction: column;
    align-items: center;
    justify-content: center;
    line-height: 1;
  }
  .disc__names { font-size: 50px; line-height: 44px; }
  .disc__age { font-size: 172px; line-height: 128px; letter-spacing: -3px; margin-top: 6px; }
  .disc__word { font-size: 88px; line-height: 72px; margin-top: 2px; }
</style>
</head>
<body>
  <main class="cover">
    <div class="cover__backdrop" role="img" aria-label="Blurred photograph of night city lights in pink, purple and teal bokeh"></div>

    <section class="venue">
      <p class="venue__line">The Basement of</p>
      <p class="venue__line">The Walrus Hotel</p>
      <p class="venue__address">214 Corran St. Halvey</p>
    </section>

    <div class="disc">
      <p class="disc__names">Oliver+Rory's</p>
      <p class="disc__age">30TH</p>
      <p class="disc__word">Birthday</p>
    </div>

    <section class="when">
      <p class="when__date">2nd August</p>
      <p class="when__time">8PM-3AM</p>
    </section>

    <p class="badge badge--venue">The<br>Walrus</p>
    <p class="badge badge--host">Quiet<br>Heron</p>
  </main>
</body>
</html>
```